Sleek wordpress site for Bramblecrest finishing works

We are a commercial job shop that serves B2B, govt & LEO and retail clients.We need a wordpress site with 6 individual pages: homepage, coating, laser engraving, laser cutting, part marking, and contact us. I have attached an outline of the desired flow and sub headings for each page. I would like to incorporate the colors of the logo through out the site to be clean and sleek enough to appeal to B2B commercial clients yet be inviting enough for retail clients.

I would like to have easy picture functionality so photographs on each page can be updated easily.

Target Market(s)

B2B industrial & Govt and Military part marking, laser engraving and coating: machine shops, aerospace companies, tool manufactures. Retail: personalized gifts, Job Shop

Coding

Coded - Design and coding required

Font styles to use
Sans Serif
Other font styles liked:
• Open to suggestion

Colors
0255a3
3176b5
eaf1f7
cfdeed
ffffff

Requirements
Must have
• Clean easy to navigate flow, separate pages as indicated on attached outline, high class feel. Great picture functionality, professional and inviting feel,
• **update: needs to be optimized for mobile, should have a gallery function. Gallery can be an additional page or embedded
Nice to have
• Social media connectivity links,
Should not have
• crappy plugins that make back-end management difficult, no blog

```html
<!DOCTYPE html>
<html lang="en">
<head>
<meta charset="utf-8">
<title>Bramblecrest Finishing Works</title>
<link href="https://fonts.googleapis.com/css2?family=Poppins:wght@300;400;500;600;700&family=Raleway:wght@300;400;700&display=swap" rel="stylesheet">
<style>
:root{
  --blue:#0255a3;
  --blue-mid:#3176b5;
  --blue-deep:#0d3d8c;
  --blue-pale:#eaf1f7;
  --blue-soft:#cfdeed;
  --white:#ffffff;
  --ink:#1e1e1e;
  --muted:#555b66;
  --star:#f3a21b;
  --line:#d4d8de;
  --footer-bg:#f6f6f7;
}
*{box-sizing:border-box;margin:0;padding:0}
html,body{width:1200px;height:3364px;overflow:hidden}
body{font-family:"Poppins",sans-serif;color:var(--ink);background:var(--white);position:relative}
.abs{position:absolute}
.btn{position:absolute;display:flex;align-items:center;justify-content:center;border-radius:22px;font-weight:600;font-size:15px;background:var(--blue-deep);color:var(--white)}

/* header */
.site-header{position:absolute;left:0;top:0;width:1200px;height:146px;background:var(--white)}
.brand{position:absolute;left:85px;top:30px;display:flex;align-items:center;gap:12px}
.brand-dot{width:54px;height:54px;border-radius:50%;background:var(--blue)}
.brand-name{font-weight:700;font-size:19px;line-height:24px;color:var(--blue);text-transform:uppercase;width:170px}
.search{position:absolute;left:635px;top:18px;width:235px;height:38px;border-radius:19px;background:#f1f2f4;border:1px solid #e2e4e8;font-size:13px;color:#8a8f98;padding:10px 16px}
.search-btn{position:absolute;right:4px;top:4px;width:28px;height:28px;border-radius:50%;background:var(--blue)}
.head-social{position:absolute;top:28px;width:16px;height:16px;border-radius:50%;border:2px solid var(--blue-deep)}
.login{left:967px;top:18px;width:145px;height:38px;font-weight:500;font-size:15px}
.main-nav{position:absolute;top:92px;left:0;width:1200px;height:24px;font-size:15px;color:#2a2a2a}
.main-nav span{position:absolute;top:0}
.main-nav .active{font-weight:700;color:#111}

/* hero */
.hero{position:absolute;left:0;top:146px;width:1200px;height:580px;background:radial-gradient(ellipse at 50% 85%,#f7c37a 0%,#c7663a 18%,#5a3a58 45%,#1f2447 75%,#141a33 100%)}
.hero-title{position:absolute;width:1200px;text-align:center;color:var(--white);font-family:"Raleway",sans-serif}
.hero-welcome{top:172px;font-weight:300;font-size:38px;letter-spacing:1px}
.hero-name{top:228px;font-weight:700;font-size:37px;font-family:"Poppins",sans-serif}
.hero-sub{top:288px;font-size:19px;font-family:"Poppins",sans-serif}
.hero .btn{top:350px;height:42px;width:128px;background:var(--blue)}
.torn-edge{position:absolute;left:0;width:1200px}

/* about */
.section-title{position:absolute;font-weight:700;color:var(--blue-deep)}
.title-mark{position:absolute;height:3px;background:var(--blue-deep)}
.about-text{position:absolute;left:103px;top:872px;width:490px;font-size:15px;line-height:30px;color:#333}
.social-dot{position:absolute;width:16px;height:16px;border-radius:50%;background:var(--blue-deep)}

/* services */
.services{position:absolute;left:0;top:1184px;width:1200px;height:604px;background:radial-gradient(ellipse at 20% 70%,#a8561f 0%,#5b3218 35%,#1d1512 75%),#1d1512}
.card{position:absolute;top:1317px;width:302px;height:381px;background:var(--white);text-align:center}
.card.featured{background:var(--blue-deep);color:var(--white)}
.card-icon{position:absolute;left:111px;top:40px;width:80px;height:80px;border-radius:50%;background:var(--blue-deep);display:flex;align-items:center;justify-content:center}
.card.featured .card-icon{background:var(--white)}
.card h3{position:absolute;top:134px;width:100%;font-size:21px;font-weight:600;color:var(--blue-deep)}
.card.featured h3{color:var(--white)}
.card p{position:absolute;top:180px;left:12px;width:278px;font-size:14px;line-height:30px}
.card .btn{top:290px;left:81px;width:140px;height:46px}
.card.featured .btn{background:var(--white);color:var(--blue-deep)}

/* testimonials */
.testimonials{position:absolute;left:0;top:1788px;width:1200px;height:489px;background:#f7f7f8}
.avatar{position:absolute;width:84px;height:84px;border-radius:50%}
.t-name{position:absolute;font-size:21px;font-weight:700;color:var(--blue-deep)}
.stars{position:absolute;font-size:22px;color:var(--star);letter-spacing:2px}
.t-text{position:absolute;width:430px;font-size:12px;line-height:26px;color:#333}

/* contact */
.contact-photo{position:absolute;left:0;top:2277px;width:1200px;height:640px;background:radial-gradient(ellipse at 78% 62%,#f2a15a 0%,#8a6a55 20%,#4d5863 48%,#2d3640 80%)}
.form-card{position:absolute;left:85px;top:2344px;width:518px;height:464px;background:var(--white);box-shadow:0 4px 20px rgba(0,0,0,.2)}
.field{position:absolute;border:1px solid var(--line);background:var(--white);font-size:12px;color:#8a8f98;padding:10px 14px}

/* footer */
.footer{position:absolute;left:0;top:2900px;width:1200px;height:386px;background:var(--footer-bg)}
.f-head{position:absolute;top:2980px;font-size:18px;font-weight:600;color:#111;letter-spacing:.3px}
.f-text{position:absolute;font-size:13px;line-height:22px;color:#333}
.f-circle{position:absolute;width:30px;height:30px;border-radius:50%;border:2px solid var(--blue-deep)}
.quick{position:absolute;left:969px;top:3030px;list-style:none;font-size:13px;line-height:24px;color:#222}
.quick li::before{content:"";display:inline-block;width:0;height:0;border-left:5px solid #222;border-top:4px solid transparent;border-bottom:4px solid transparent;margin-right:10px}
.copyright{position:absolute;left:0;top:3286px;width:1200px;height:78px;background:var(--white);border-top:1px solid #e5e5e5;text-align:center;font-size:13px;line-height:76px;color:#333}
</style>
</head>
<body>

<header class="site-header">
  <div class="brand"><div class="brand-dot"></div><div class="brand-name">Bramblecrest Finishing Works</div></div>
  <div class="search">Search<div class="search-btn"></div></div>
  <div class="head-social" style="left:888px"></div>
  <div class="head-social" style="left:916px"></div>
  <div class="btn login">Login / Register</div>
  <nav class="main-nav">
    <span class="active" style="left:420px">Home</span>
    <span style="left:505px">Coating</span>
    <span style="left:603px">Laser Engraving</span>
    <span style="left:763px">Laser Cutting</span>
    <span style="left:899px">Part Marking</span>
    <span style="left:1030px">Contact Us</span>
  </nav>
</header>

<section class="hero" role="img" aria-label="Laser cutting machine throwing sparks">
  <div class="hero-title hero-welcome">WELCOME TO</div>
  <div class="hero-title hero-name">BRAMBLECREST FINISHING WORKS</div>
  <div class="hero-title hero-sub">Sed ut perspiciatis unde omnis iste natus error sit voluptatem</div>
  <div class="btn" style="left:464px">Read More</div>
  <div class="btn" style="left:608px">Contact Us</div>
</section>
<svg class="torn-edge" style="top:666px" width="1200" height="64" viewBox="0 0 1200 64"><path d="M0 30 L14 26 L26 31 L40 24 L55 29 L68 22 L82 28 L96 25 L110 32 L124 26 L138 30 L152 23 L166 28 L180 26 L195 33 L209 27 L222 30 L236 22 L250 29 L264 25 L278 31 L292 24 L306 28 L320 23 L334 30 L348 26 L362 32 L376 25 L390 29 L404 22 L418 28 L432 26 L446 33 L460 27 L474 30 L488 23 L502 29 L516 25 L530 31 L544 24 L558 30 L572 26 L586 32 L600 27 L614 31 L628 34 L642 30 L656 25 L670 31 L684 24 L698 29 L712 26 L726 32 L740 23 L754 28 L768 25 L782 31 L796 24 L810 29 L824 22 L838 28 L852 26 L866 33 L880 27 L894 30 L908 23 L922 29 L936 25 L950 31 L964 24 L978 28 L992 22 L1006 29 L1020 26 L1034 32 L1048 25 L1062 30 L1076 23 L1090 28 L1104 26 L1118 32 L1132 24 L1146 29 L1160 25 L1174 31 L1188 26 L1200 29 V64 H0Z" fill="#ffffff"/><circle cx="633" cy="40" r="14" fill="#ffffff"/></svg>

<section class="about">
  <h2 class="section-title" style="left:108px;top:812px;font-size:27px">About us</h2>
  <div class="title-mark" style="left:110px;top:853px;width:52px"></div>
  <p class="about-text">Lorem ipsum dolor sit amet, consectetur adipisicing elit, sed do eiusmod tempor incidunt ut labore et dolore magna aliqua. Ut enim ad minim veniam, quis nostrud exerciti aulamco laboris nisi ut aliquip ex ea commodo consequat. Duis aute irure dolor in reprehederit essete cillum dolore eu fugiat nulla pariatur.</p>
  <div class="btn" style="left:103px;top:1041px;width:137px;height:44px">Read More</div>
  <div class="social-dot" style="left:266px;top:1054px"></div>
  <div class="social-dot" style="left:302px;top:1054px"></div>
  <div class="social-dot" style="left:342px;top:1054px"></div>
  <div class="social-dot" style="left:384px;top:1054px"></div>
  <div class="social-dot" style="left:428px;top:1054px"></div>
  <div class="social-dot" style="left:470px;top:1054px"></div>
  <svg class="abs" style="left:615px;top:788px" width="465" height="332" viewBox="0 0 465 332"><polygon points="30,60 465,0 430,225 150,332 0,332" fill="#0d3d8c"/></svg>
  <div class="abs" role="img" aria-label="Laser head cutting a metal sheet" style="left:645px;top:800px;width:420px;height:310px;clip-path:polygon(8% 0,100% 0,92% 100%,0 100%);background:linear-gradient(135deg,#3a4048 0%,#8a8e90 40%,#f0c48a 58%,#5b5f63 80%,#2b2f33 100%)"></div>
</section>

<section class="services">
  <h2 class="section-title" style="left:0;width:1200px;text-align:center;top:66px;font-size:25px;color:var(--white)">Our Services</h2>
  <div class="title-mark" style="left:520px;top:104px;width:54px;background:var(--white)"></div>
</section>
<article class="card" style="left:121px">
  <div class="card-icon"><svg width="40" height="40" viewBox="0 0 40 40"><path d="M8 32 L11 23 L27 7 L33 13 L17 29 Z M11 23 L17 29" fill="none" stroke="#fff" stroke-width="2.5" stroke-linejoin="round"/></svg></div>
  <h3>Laser engraving</h3>
  <p>Morbi semper, dui sodales aliquet imperdiet, lacus ligula congue neque, quis pretium lectus libero id.</p>
  <div class="btn">Read More</div>
</article>
<article class="card featured" style="left:446px">
  <div class="card-icon"><svg width="40" height="40" viewBox="0 0 40 40"><rect x="8" y="6" width="24" height="6" fill="#0d3d8c"/><rect x="16" y="12" width="8" height="10" fill="#0d3d8c"/><path d="M20 22 V30" stroke="#0d3d8c" stroke-width="2"/><rect x="6" y="31" width="28" height="4" fill="#0d3d8c"/></svg></div>
  <h3>Laser Cutting</h3>
  <p>Morbi semper, dui sodales aliquet imperdiet, lacus ligula congue neque, quis pretium lectus libero id.</p>
  <div class="btn">Read More</div>
</article>
<article class="card" style="left:776px">
  <div class="card-icon"><svg width="40" height="40" viewBox="0 0 40 40"><rect x="6" y="8" width="12" height="24" fill="none" stroke="#fff" stroke-width="2.5"/><rect x="22" y="16" width="12" height="16" fill="none" stroke="#fff" stroke-width="2.5"/><path d="M10 14 H14 M10 20 H14 M26 22 H30" stroke="#fff" stroke-width="2"/></svg></div>
  <h3>Part Marking</h3>
  <p>Morbi semper, dui sodales aliquet imperdiet, lacus ligula congue neque, quis pretium lectus libero id.</p>
  <div class="btn">Read More</div>
</article>
<svg class="abs" style="left:576px;top:1727px" width="48" height="20" viewBox="0 0 48 20"><circle cx="10" cy="10" r="7" fill="none" stroke="#fff" stroke-width="2"/><circle cx="36" cy="10" r="7" fill="#fff"/></svg>

<section class="testimonials">
  <h2 class="section-title" style="left:0;width:1200px;text-align:center;top:58px;font-size:25px">Testimonials</h2>
  <div class="title-mark" style="left:520px;top:98px;width:54px"></div>
</section>
<div class="avatar" role="img" aria-label="Portrait of Jack" style="left:123px;top:1951px;background:linear-gradient(160deg,#c9cdd2,#7a6a5e)"></div>
<div class="t-name" style="left:220px;top:1958px">Jack</div>
<div class="stars" style="left:220px;top:2002px">★★★★★</div>
<p class="t-text" style="left:123px;top:2044px">Lorem Ipsum is simply dummy text of the printing and typesetting industry. Lorem Ipsum has been the industry's standard dummy text ever since the 1500s, when an unknown printer took a galley of type and scrambled it to make a type specimen book.</p>
<div class="avatar" role="img" aria-label="Portrait of John" style="left:646px;top:1951px;background:linear-gradient(160deg,#d8dde3,#6f7d90)"></div>
<div class="t-name" style="left:748px;top:1958px">John</div>
<div class="stars" style="left:748px;top:2002px">★★★★★</div>
<p class="t-text" style="left:646px;top:2044px">Lorem Ipsum is simply dummy text of the printing and typesetting industry. Lorem Ipsum has been the industry's standard dummy text ever since the 1500s, when an unknown printer took a galley of type and scrambled it to make a type specimen book.</p>

<section class="contact-photo" role="img" aria-label="Milling machine cutting metal with sparks"></section>
<form class="form-card">
  <h2 class="section-title" style="left:47px;top:38px;font-size:26px">Get in Touch</h2>
  <div class="field" style="left:47px;top:94px;width:200px;height:45px">Name</div>
  <div class="field" style="left:269px;top:94px;width:202px;height:45px">Zipcode</div>
  <div class="field" style="left:47px;top:164px;width:200px;height:45px">Email</div>
  <div class="field" style="left:269px;top:164px;width:202px;height:45px">Phone number</div>
  <div class="field" style="left:47px;top:229px;width:424px;height:130px">Message</div>
  <div class="btn" style="left:47px;top:381px;width:139px;height:38px;font-size:13px">Submit</div>
</form>

<footer class="footer"></footer>
<svg class="torn-edge" style="top:2866px" width="1200" height="40" viewBox="0 0 1200 40"><path d="M0 14 L14 10 L28 16 L42 9 L56 14 L70 8 L84 13 L98 11 L112 17 L126 10 L140 15 L154 8 L168 13 L182 11 L196 18 L210 12 L224 15 L238 7 L252 14 L266 10 L280 16 L294 9 L308 13 L322 8 L336 15 L350 11 L364 17 L378 10 L392 14 L406 7 L420 13 L434 11 L448 18 L462 12 L476 15 L490 8 L504 14 L518 10 L532 16 L546 12 L560 17 L574 11 L588 15 L602 9 L616 14 L630 11 L644 16 L658 8 L672 13 L686 10 L700 16 L714 9 L728 14 L742 7 L756 13 L770 11 L784 18 L798 12 L812 15 L826 8 L840 14 L854 10 L868 16 L882 9 L896 13 L910 7 L924 14 L938 11 L952 17 L966 10 L980 15 L994 8 L1008 13 L1022 11 L1036 17 L1050 9 L1064 14 L1078 10 L1092 16 L1106 11 L1120 14 L1134 9 L1148 15 L1162 10 L1176 16 L1190 11 L1200 13 V40 H0Z" fill="#f6f6f7"/><circle cx="558" cy="22" r="10" fill="#f6f6f7"/></svg>
<div class="abs" style="left:117px;top:2995px;display:flex;align-items:center;gap:8px">
  <div style="width:34px;height:34px;border-radius:50%;background:var(--blue)"></div>
  <div style="font-weight:700;font-size:13px;line-height:16px;color:var(--blue);width:110px;text-transform:uppercase">Bramblecrest Finishing Works</div>
</div>
<div class="f-circle" style="left:117px;top:3087px"></div>
<div class="f-circle" style="left:157px;top:3087px"></div>
<div class="f-circle" style="left:197px;top:3087px"></div>

<h3 class="f-head" style="left:318px">CONTACT US</h3>
<svg class="abs" style="left:320px;top:3042px" width="14" height="18" viewBox="0 0 14 18"><path d="M7 17 C2 11 1 9 1 6.5 A6 6 0 0 1 13 6.5 C13 9 12 11 7 17Z" fill="#0d3d8c"/><circle cx="7" cy="6.5" r="2.2" fill="#fff"/></svg>
<p class="f-text" style="left:352px;top:3038px">418 W Alder Lane #7,<br>Tempe, AZ 85281</p>
<svg class="abs" style="left:320px;top:3091px" width="15" height="15" viewBox="0 0 15 15"><path d="M3 1 L6 4 L4.5 6 Q6 9 9 10.5 L11 9 L14 12 L12 14 Q6 14 1 3 Z" fill="#0d3d8c"/></svg>
<p class="f-text" style="left:352px;top:3090px">Phone: (480) 555 - 0142</p>
<svg class="abs" style="left:320px;top:3124px" width="15" height="11" viewBox="0 0 15 11"><rect width="15" height="11" fill="#0d3d8c"/><path d="M0 0 L7.5 6 L15 0" fill="none" stroke="#fff" stroke-width="1.3"/></svg>
<p class="f-text" style="left:352px;top:3120px">Email: info@bramblecrestworks.com</p>

<h3 class="f-head" style="left:619px">SIGN UP FOR NEWSLETTER</h3>
<p class="f-text" style="left:619px;top:3032px;width:310px;font-size:12px">Want to make an impact? Provide your email and we'll be in touch.</p>
<div class="field" style="left:619px;top:3091px;width:297px;height:40px;font-size:11px">Enter email</div>
<div class="btn" style="left:619px;top:3149px;width:123px;height:36px">SIGN UP</div>

<h3 class="f-head" style="left:969px">QUICK LINKS</h3>
<ul class="quick">
  <li>Home</li><li>Coating</li><li>Laser Engraving</li><li>Laser Cutting</li><li>Part Marking</li><li>Contact Us</li>
</ul>

<div class="copyright">Copyrights © 2018 All Rights Reserved</div>
</body>
</html>
```